BorrowNest Website design, we are a home loan / lending company

We are a finance broking company that can do mortgages / home loans, Car Loans, Commercial Loans, SMSF Loans, Business Loans, Personal Loans
We are looking for a simple website, not too busy, easy to navigate, something that prompts customers to action or call us.
I like the simplicity of the following websites:
https://www.velkarafinance.com.au/ - I like this website front page. I was thinking I have my logo, the one with the black background appear , then the toolbar at the top perhaps?
https://trevix.com.au/business-loans# - on this page there are images under finance that works for you that I like that concept.
https://dunmerel.com.au/contact/ - I like the Make an Appointment page
https://trevix.com.au/about-us - Simple but effective page design

Target Market(s)

Home Loan Customer

Industry/Entity Type

Finance / Home Loans

Coding

Coded - Design and coding required

Number of Pages Required

5+ page

Font styles to use
Serif

Colors
0094D4
00A9DD
6FCCEA
C7EBF8
E9F6FB

Requirements
Must have
• The following Heading s - Contact Us, About Us, Our People, Make an Appointment, Loan Options, Calculators, Reviews. I want to use the Logo colours I have in the zip files I uploaded.
Nice to have
• Simple clean design

```html
<!DOCTYPE html>
<html lang="en">
<head>
<meta charset="utf-8">
<title>BorrowNest – Home Loans &amp; Lending</title>
<link href="https://fonts.googleapis.com/css2?family=Roboto:wght@400;500;700&display=swap" rel="stylesheet">
<style>
:root{
  --brand:#0094D4;
  --brand-2:#00A9DD;
  --brand-3:#6FCCEA;
  --brand-4:#C7EBF8;
  --tint:#E9F6FB;
  --ink:#111111;
  --text:#555555;
  --white:#ffffff;
  --footer:#000000;
}
*{margin:0;padding:0;box-sizing:border-box}
html,body{width:1200px;height:3795px;overflow:hidden;background:var(--white)}
body{position:relative;font-family:'Roboto',Arial,sans-serif;color:var(--text)}
.abs{position:absolute}
.topline{left:0;top:0;width:1200px;height:5px;background:var(--brand-2)}
.logo{font-family:'Roboto',Arial,sans-serif;font-weight:700;color:#333;font-size:34px;letter-spacing:-0.5px;line-height:1}
.nav{top:41px;left:405px;display:flex;gap:25px;font-size:14px;color:#333;text-transform:uppercase}
.nav a{color:inherit;text-decoration:none}
.nav .active{color:var(--brand-2);border-bottom:2px solid var(--brand-2);padding-bottom:4px}
.btn{display:flex;align-items:center;justify-content:center;gap:10px;background:var(--brand-2);color:var(--white);font-weight:700;font-size:15px;border-radius:26px;text-transform:uppercase}
.btn .arr{width:14px;height:14px;border-radius:50%;background:var(--white);position:relative}
.btn .arr::after{content:"";position:absolute;left:4px;top:4px;border-left:6px solid var(--brand-2);border-top:3px solid transparent;border-bottom:3px solid transparent}
.hero-title{left:648px;color:var(--white);font-weight:700}
.dot{width:13px;height:13px;border-radius:50%;background:var(--white);top:795px}
.section-title{left:0;width:1200px;text-align:center;font-size:31px;font-weight:500;color:var(--ink)}
.rule{width:72px;height:2px;background:var(--brand-2);left:564px}
.rule::after{content:"";position:absolute;left:30px;top:-4px;width:10px;height:10px;border-radius:50%;background:var(--brand-2)}
.rule.light{background:var(--white)}
.rule.light::after{background:var(--white)}
.lead{left:200px;width:800px;text-align:center;font-size:14px;line-height:22px}
.card{width:226px;height:310px;top:1108px;background:var(--white);box-shadow:0 0 8px rgba(0,0,0,.12);border-radius:4px}
.card .photo{position:absolute;left:10px;top:12px;width:206px;height:130px}
.card .icon{position:absolute;right:18px;top:117px;width:44px;height:44px;border-radius:50%;background:var(--white);box-shadow:0 0 4px rgba(0,0,0,.2);display:flex;align-items:center;justify-content:center}
.card h3{position:absolute;left:18px;top:171px;font-size:15px;font-weight:500;color:var(--ink)}
.card .bar{position:absolute;left:18px;top:198px;width:30px;height:2px;background:var(--brand-2)}
.card p{position:absolute;left:18px;top:210px;width:195px;font-size:14px;line-height:25px}
.card .more{position:absolute;left:18px;top:271px;font-size:14px;font-weight:700;color:var(--brand-2);display:flex;align-items:center;gap:12px}
.card .more i{width:13px;height:13px;border-radius:50%;background:var(--brand-2);position:relative}
.card .more i::after{content:"";position:absolute;left:4px;top:3.5px;border-left:5px solid var(--white);border-top:3px solid transparent;border-bottom:3px solid transparent}
.card.is-active{background:var(--brand-2);outline:2px solid var(--brand-2);outline-offset:2px}
.card.is-active h3,.card.is-active p,.card.is-active .more{color:var(--white)}
.card.is-active .bar{background:var(--white)}
.card.is-active .more i{background:var(--white)}
.card.is-active .more i::after{border-left-color:var(--brand-2)}
.chev{width:12px;height:12px;border-left:2px solid #222;border-bottom:2px solid #222;top:1262px}
.about-band{left:0;top:1507px;width:1200px;height:608px;background:var(--tint)}
.about-text{left:587px;top:1671px;width:501px;font-size:14px;line-height:24px;text-align:justify}
.review{width:305px;height:232px;top:2281px;background:var(--white);box-shadow:0 0 8px rgba(0,0,0,.1)}
.review .stars{position:absolute;left:15px;top:41px;color:#f1b500;font-size:12px;letter-spacing:1px}
.review .name{position:absolute;left:15px;top:63px;font-size:15px;font-weight:500;color:var(--brand-2)}
.review .avatar{position:absolute;right:36px;top:32px;width:58px;height:58px;border-radius:50%}
.review p{position:absolute;left:22px;top:112px;width:262px;font-size:13px;line-height:26px;text-align:justify}
.review.is-active{background:var(--brand-2);outline:2px solid var(--brand-2);outline-offset:3px}
.review.is-active .stars{color:#f1d000}
.review.is-active .name,.review.is-active p{color:var(--white)}
.contact-band{left:0;top:2620px;width:1200px;height:820px;background:linear-gradient(120deg,#1a9ad6,#0c86c6 55%,#2aa5df)}
.field{background:var(--white);height:43px;display:flex;align-items:center;padding-left:24px;gap:14px;font-size:13px;color:#333}
.field svg{flex:none}
.foot-h{top:3425px;color:var(--white);font-size:15px;font-weight:700;text-transform:uppercase}
.foot-h::after{content:"";position:absolute;left:0;top:26px;width:36px;height:2px;background:var(--brand-2)}
.foot-links{top:3476px;list-style:none;color:var(--white);font-size:15px}
.foot-links li{height:36px;display:flex;gap:18px;align-items:center}
.foot-links li::before{content:"»";font-size:15px}
.ci{left:112px;display:flex;align-items:center;gap:14px;color:var(--white);font-size:15px;line-height:25px}
.ci .ring{width:34px;height:34px;border-radius:50%;background:#262626;display:flex;align-items:center;justify-content:center;flex:none}
.foot-about{left:855px;top:3478px;width:233px;color:var(--white);font-size:15px;line-height:26px;text-align:center}
</style>
</head>
<body>

<div class="abs topline"></div>

<!-- Header -->
<div class="abs logo" style="left:112px;top:30px">BorrowNest</div>
<nav class="abs nav">
  <a class="active">Home</a><a>About Us</a><a>Our People</a><a>Reviews</a><a>Contact Us</a>
</nav>
<div class="abs btn" style="left:880px;top:27px;width:208px;height:48px;font-size:14px">Make an Appointment</div>

<!-- Hero -->
<svg class="abs" style="left:0;top:95px" width="1200" height="800" viewBox="0 0 1200 800">
  <defs>
    <linearGradient id="heroPhoto" x1="0" y1="0" x2="1" y2="1">
      <stop offset="0" stop-color="#5a5f58"/>
      <stop offset=".45" stop-color="#8c8f88"/>
      <stop offset="1" stop-color="#c9cbc6"/>
    </linearGradient>
  </defs>
  <path d="M0 600 C 250 830, 820 840, 1200 630 V660 C 820 860, 250 850, 0 620 Z" fill="var(--brand-3)"/>
  <path d="M0 598 C 250 818, 820 830, 1200 630 V644 C 820 846, 250 836, 0 612 Z" fill="var(--brand-2)"/>
  <path role="img" aria-label="Photo of a man writing notes beside a laptop" d="M0 0 H1200 V630 C 820 830, 250 818, 0 598 Z" fill="url(#heroPhoto)"/>
</svg>
<div class="abs hero-title" style="top:338px;font-size:40px">Welcome To</div>
<div class="abs hero-title" style="top:398px;left:643px;font-size:74px">BorrowNest</div>
<div class="abs btn" style="left:648px;top:523px;width:176px;height:52px">Get Started <span class="arr"></span></div>
<div class="abs btn" style="left:838px;top:523px;width:178px;height:52px">Loan Options <span class="arr"></span></div>
<div class="abs dot" style="left:559px"></div>
<div class="abs dot" style="left:582px;background:var(--brand-2)"></div>
<div class="abs dot" style="left:605px"></div>
<div class="abs dot" style="left:628px"></div>

<!-- What We Do -->
<h2 class="abs section-title" style="top:953px">What We Do</h2>
<div class="abs rule" style="top:1001px"></div>
<p class="abs lead" style="top:1031px">Lorem ipsum dolor sit amet consectetur adipiscing elit doeiusmod tempor incididunt labore dolore magna enim ad minim veniam, quis nostrud exercitation ullamco laboris nisi ut aliquip&nbsp; commodo consequat.</p>

<div class="abs chev" style="left:60px;transform:rotate(45deg)"></div>
<div class="abs chev" style="left:1130px;transform:rotate(-135deg)"></div>

<div class="abs card" style="left:112px">
  <div class="photo" role="img" aria-label="Photo of a home loan consultation" style="background:linear-gradient(135deg,#4a3b30,#8a7463)"></div>
  <div class="icon"><svg width="24" height="24" viewBox="0 0 24 24" fill="none" stroke="var(--brand-2)" stroke-width="1.6"><path d="M4 11 12 4l8 7M6 10v9h12v-9"/><path d="M10 19v-5h4v5"/></svg></div>
  <h3>Home loans</h3><div class="bar"></div>
  <p>Lorem ipsum dolor sit amet consectetur adipiscing elitd</p>
  <div class="more">Read More <i></i></div>
</div>
<div class="abs card" style="left:362px">
  <div class="photo" role="img" aria-label="Photo of a car loan agreement being signed" style="background:linear-gradient(135deg,#3c3c3c,#a8a8a6)"></div>
  <div class="icon"><svg width="24" height="24" viewBox="0 0 24 24" fill="none" stroke="var(--brand-2)" stroke-width="1.6"><path d="M4 15l2-5h12l2 5v3H4z"/><circle cx="8" cy="18" r="1.5"/><circle cx="16" cy="18" r="1.5"/></svg></div>
  <h3>Car Loans</h3><div class="bar"></div>
  <p>Lorem ipsum dolor sit amet consectetur adipiscing elitd</p>
  <div class="more">Read More <i></i></div>
</div>
<div class="abs card is-active" style="left:612px">
  <div class="photo" role="img" aria-label="Photo of a commercial loan meeting" style="background:linear-gradient(135deg,#2b3340,#9aa2ab)"></div>
  <div class="icon"><svg width="24" height="24" viewBox="0 0 24 24" fill="none" stroke="var(--brand-2)" stroke-width="1.6"><rect x="6" y="5" width="12" height="15"/><path d="M9 9h2M13 9h2M9 13h2M13 13h2M11 20v-3h2v3"/></svg></div>
  <h3>Commercial Loans</h3><div class="bar"></div>
  <p>Lorem ipsum dolor sit amet consectetur adipiscing elitd</p>
  <div class="more">Read More <i></i></div>
</div>
<div class="abs card" style="left:862px">
  <div class="photo" role="img" aria-label="Photo of a couple reviewing a business loan" style="background:linear-gradient(135deg,#6d7885,#d8d6d0)"></div>
  <div class="icon"><svg width="24" height="24" viewBox="0 0 24 24" fill="none" stroke="var(--brand-2)" stroke-width="1.6"><rect x="4" y="8" width="16" height="11" rx="1"/><path d="M9 8V6h6v2M4 13h16"/></svg></div>
  <h3>Business Loans</h3><div class="bar"></div>
  <p>Lorem ipsum dolor sit amet consectetur adipiscing elitd</p>
  <div class="more">Read More <i></i></div>
</div>

<!-- About -->
<div class="abs about-band"></div>
<svg class="abs" style="left:90px;top:1580px" width="470" height="470" viewBox="0 0 470 470">
  <defs>
    <linearGradient id="aboutPhoto" x1="0" y1="0" x2="1" y2="1">
      <stop offset="0" stop-color="#cfd6dc"/>
      <stop offset=".55" stop-color="#8b95a1"/>
      <stop offset="1" stop-color="#2f4f7a"/>
    </linearGradient>
  </defs>
  <circle cx="232" cy="232" r="230" fill="var(--brand-4)" opacity=".6"/>
  <circle cx="232" cy="232" r="226" fill="var(--brand-2)"/>
  <circle role="img" aria-label="Photo of two colleagues discussing a document" cx="232" cy="232" r="214" fill="url(#aboutPhoto)"/>
</svg>
<h2 class="abs" style="left:587px;top:1593px;font-size:31px;font-weight:500;color:var(--ink)">About us</h2>
<div class="abs rule" style="left:587px;top:1639px"></div>
<p class="abs about-text">Lorem ipsum dolor sit amet, consectetur adipiscing elit, sed do eiusmod tempor incididunt ut labore et dolore magna aliqua. Ut enim ad minim veniam, quis nostrud exercitation ullamco laboris nisi ut aliquip ex ea commodo consequat. Duis aute irure dolor in reprehenderit in voluptate velit esse cillum dolore eu fugiat nulla pariatur. Excepteur sint occaecat cupidatat non proident, sunt in culpa qui officia deserunt mollit anim id est laborum.Lorem ipsum dolor sit amet, consectetur adipiscing elit, sed do eiusmod tempor incididunt ut labore et dolore magna aliqua. Ut enim ad minim veniam, quis nostrud exercitation ullamco laboris nisi ut aliquip ex ea commodo consequat. Duis aute irure dolor in reprehenderit in voluptate velit esse cillum dolore eu fugiat occaecat cupidatat non proident, sunt in culpa qui officia deserunt.</p>
<div class="abs btn" style="left:587px;top:1970px;width:178px;height:52px">Learn More <span class="arr"></span></div>
<div class="abs btn" style="left:777px;top:1970px;width:178px;height:52px">Calculators <span class="arr"></span></div>

<!-- Reviews -->
<h2 class="abs section-title" style="top:2192px">Client Reviews</h2>
<div class="abs rule" style="top:2240px"></div>

<div class="abs review" style="left:121px">
  <div class="stars">★★★★★</div><div class="name">Mara Quill</div>
  <div class="avatar" role="img" aria-label="Client portrait" style="background:linear-gradient(135deg,#c9b29a,#6b5a4a)"></div>
  <p>Lorem ipsum dolor sit amet, consectetur adipiscing elited sed doin eiusmod tempor incididunt ut labore et dolore magna aliqua Uenim adet minim veniam quis nostrud.</p>
</div>
<div class="abs review is-active" style="left:447px;width:308px">
  <div class="stars">★★★★★</div><div class="name">Tobin Ashe</div>
  <div class="avatar" role="img" aria-label="Client portrait" style="background:linear-gradient(135deg,#d9d9d9,#5d6f86)"></div>
  <p>Lorem ipsum dolor sit amet, consectetur adipiscing elited sed doin eiusmod tempor incididunt ut labore et dolore magna aliqua Uenim adet minim veniam quis nostrud.</p>
</div>
<div class="abs review" style="left:774px">
  <div class="stars">★★★★★</div><div class="name">Elio Vance</div>
  <div class="avatar" role="img" aria-label="Client portrait" style="background:linear-gradient(135deg,#e0e0e0,#2a2a2a)"></div>
  <p>Lorem ipsum dolor sit amet, consectetur adipiscing elited sed doin eiusmod tempor incididunt ut labore et dolore magna aliqua Uenim adet minim veniam quis nostrud.</p>
</div>

<!-- Get in Touch -->
<div class="abs contact-band" role="img" aria-label="Blue-tinted photo of an office workspace"></div>
<h2 class="abs section-title" style="top:2696px;color:var(--white)">Get in Touch</h2>
<div class="abs rule light" style="top:2744px"></div>

<div class="abs field" style="left:160px;top:2781px;width:433px">
  <svg width="10" height="12" viewBox="0 0 10 12"><circle cx="5" cy="3" r="3" fill="#222"/><path d="M0 12c0-4 2-5 5-5s5 1 5 5z" fill="#222"/></svg>First Name</div>
<div class="abs field" style="left:606px;top:2781px;width:434px">
  <svg width="10" height="12" viewBox="0 0 10 12"><circle cx="5" cy="3" r="3" fill="#222"/><path d="M0 12c0-4 2-5 5-5s5 1 5 5z" fill="#222"/></svg>Last Name</div>
<div class="abs field" style="left:160px;top:2844px;width:433px">
  <svg width="12" height="10" viewBox="0 0 12 10"><rect width="12" height="10" fill="#222"/><path d="M0 0l6 5 6-5" stroke="#fff" fill="none"/></svg>Email</div>
<div class="abs field" style="left:606px;top:2844px;width:434px">
  <svg width="8" height="12" viewBox="0 0 8 12"><rect x=".7" y=".7" width="6.6" height="10.6" rx="1" fill="none" stroke="#222" stroke-width="1.4"/></svg>Phone</div>
<div class="abs field" style="left:160px;top:2906px;width:880px;height:148px;align-items:flex-start;padding-top:16px">
  <svg width="14" height="11" viewBox="0 0 14 11"><ellipse cx="5.5" cy="4" rx="5.5" ry="4" fill="#222"/><ellipse cx="9.5" cy="7" rx="4.5" ry="3.5" fill="#222"/></svg>Comments</div>
<div class="abs btn" style="left:516px;top:3090px;width:166px;height:50px;border:2px solid var(--white)">Submit Now <span class="arr"></span></div>

<!-- Footer -->
<svg class="abs" style="left:0;top:3220px" width="1200" height="575" viewBox="0 0 1200 575">
  <path d="M0 200 C 300 -20, 900 -20, 1200 200 V575 H0 Z" fill="#5a7a90"/>
  <path d="M0 212 C 300 -8, 900 -8, 1200 212 V575 H0 Z" fill="var(--footer)"/>
</svg>

<div class="abs foot-h" style="left:112px">Contact Us</div>
<div class="abs foot-h" style="left:412px">Quick Links</div>
<div class="abs foot-h" style="left:656px">Other Links</div>

<div class="abs ci" style="top:3479px"><span class="ring"><svg width="14" height="14" viewBox="0 0 24 24"><path d="M6 3l3 4-2 2c1 3 4 6 7 7l2-2 4 3-2 3C10 20 4 14 3 5z" fill="#fff"/></svg></span>+1 555 013 2480</div>
<div class="abs ci" style="top:3539px"><span class="ring"><svg width="14" height="12" viewBox="0 0 14 12"><rect x=".7" y=".7" width="12.6" height="10.6" fill="none" stroke="#fff" stroke-width="1.4"/><path d="M1 1l6 5 6-5" stroke="#fff" fill="none" stroke-width="1.4"/></svg></span>info@borrownest.com</div>
<div class="abs ci" style="top:3606px"><span class="ring"><svg width="10" height="14" viewBox="0 0 10 14"><path d="M5 0C2 0 0 2 0 5c0 4 5 9 5 9s5-5 5-9c0-3-2-5-5-5z" fill="#fff"/><circle cx="5" cy="5" r="1.8" fill="#262626"/></svg></span>Lorem ipsum dolor sit<br>consectetur adipiscin</div>

<ul class="abs foot-links" style="left:412px">
  <li>Home</li><li>About Us</li><li>Our People</li><li>Reviews</li><li>Contact Us</li>
</ul>
<ul class="abs foot-links" style="left:656px">
  <li>Team</li><li>FAQ</li><li>Terms Of Use</li><li>Privacy Policy</li><li>Contact Us</li>
</ul>

<div class="abs logo" style="left:851px;top:3424px;color:var(--white)">BorrowNest</div>
<p class="abs foot-about">Lorem ipsum dolor consectetur adipiscing elited sed do eiusmod.</p>
<div class="abs" style="left:853px;top:3543px;width:235px;height:45px;background:var(--white);display:flex;align-items:center;justify-content:space-between;padding:0 16px;font-size:15px;color:#333">Enter email:
  <svg width="14" height="11" viewBox="0 0 14 11"><rect x=".7" y=".7" width="12.6" height="9.6" fill="none" stroke="var(--brand-2)" stroke-width="1.4"/><path d="M1 1l6 5 6-5" stroke="var(--brand-2)" fill="none" stroke-width="1.4"/></svg></div>
<div class="abs btn" style="left:853px;top:3603px;width:235px;height:45px;border-radius:0">Subscribe Now <span class="arr"></span></div>

<div class="abs" style="left:112px;top:3718px;width:976px;height:1px;background:#444"></div>
<p class="abs" style="left:0;top:3745px;width:1200px;text-align:center;color:var(--white);font-size:14px">©Copyrights 2022&nbsp; BorrowNest&nbsp; All Rights Reserved.</p>

</body>
</html>
```